Request for Business Card Design

Hi. My name is Marlene, I am looking for a new business card design for my company, Quarrow Signal Instruments, LLC. I really like the design you did for Tarsel Venture and was hoping you could do something similar using our full logo and our mark. I am also open to any raised texture design using our mark. I have attached our full logo, which would need to be somewhere on the card, as well as the mark in both outline and full form, as well as our brand colors / guide. The card does not have to be white, as long as our logo and mark appear. I actually like darker colored business cards more, but am open to all options. If you are interested in working with me, please let me know. We would also take the business card design into letterhead design if you can do that.

```html
<!DOCTYPE html>
<html lang="en">
<head>
<meta charset="utf-8">
<title>Quarrow Signal Instruments – Business Card</title>
<link rel="stylesheet" href="https://fonts.googleapis.com/css2?family=Arimo:ital,wght@0,400;0,700;1,400&display=swap">
<style>
  :root {
    --stage: #0e0e0f;
    --card: #232324;
    --card-deep: #1a1a1b;
    --brand-blue: #0096c2;
    --ink: #ffffff;
    --ink-soft: #e6e6e6;
    --relief-light: #3a3a3b;
    --relief-dark: #151516;
  }
  * { margin: 0; padding: 0; box-sizing: border-box; }
  html, body {
    width: 1200px; height: 963px; overflow: hidden;
    background: var(--stage);
    font-family: "Arimo", Arial, sans-serif;
  }
  .stage {
    width: 1200px; height: 963px;
    display: flex; align-items: center; justify-content: center; gap: 48px;
  }
  .card {
    position: relative; width: 540px; height: 310px;
    border-radius: 16px; overflow: hidden;
    background: var(--card);
    box-shadow: 0 3px 0 var(--brand-blue), 0 20px 40px rgba(0,0,0,.6);
  }

  /* Front */
  .card-front__corner {
    position: absolute; right: 0; bottom: 0; width: 100%; height: 100%;
  }
  .card-front__relief {
    position: absolute; right: 38px; bottom: 22px;
    width: 250px; height: 250px; border-radius: 50%;
    background: radial-gradient(circle at 40% 35%, var(--relief-light), var(--relief-dark) 70%);
    box-shadow: inset 0 -6px 14px rgba(0,0,0,.5);
  }
  .wordmark { position: absolute; left: 30px; top: 32px; }
  .wordmark__name {
    font-weight: 700; font-size: 38px; letter-spacing: 4px; color: var(--ink); line-height: 1;
  }
  .wordmark__line {
    font-size: 10.5px; letter-spacing: 1.6px; color: var(--ink); margin-top: 5px;
  }
  .person { position: absolute; left: 0; top: 112px; }
  .person__name {
    display: flex; align-items: center; gap: 12px;
    font-weight: 700; font-size: 19px; letter-spacing: .5px; color: var(--brand-blue);
  }
  .person__bar { width: 22px; height: 24px; background: var(--brand-blue); }
  .person__role { margin-left: 34px; margin-top: 4px; font-size: 13px; color: var(--ink-soft); }
  .contact {
    position: absolute; left: 34px; top: 178px; list-style: none;
    font-size: 13px; line-height: 20px; color: var(--ink-soft);
  }
  .contact li { display: flex; align-items: center; gap: 8px; }
  .contact svg { width: 12px; height: 12px; flex: none; }
  .contact .no-icon { padding-left: 20px; }

  /* Back */
  .card-back__pattern {
    position: absolute; inset: 0;
    background: radial-gradient(ellipse at 60% 40%, #2b2b2c, var(--card-deep) 80%);
  }
  .back-mark {
    position: absolute; left: 0; right: 0; top: 122px;
    display: flex; flex-direction: column; align-items: center;
  }
  .back-mark__row { display: flex; align-items: center; gap: 16px; }
  .back-mark__dot { width: 44px; height: 44px; border-radius: 50%; background: var(--brand-blue); }
  .back-mark__name { font-weight: 700; font-size: 40px; letter-spacing: 4px; color: var(--ink); }
  .back-mark__line { margin-top: 6px; margin-left: 60px; font-size: 11px; letter-spacing: 1.8px; color: var(--ink); }
</style>
</head>
<body>
<main class="stage">

  <section class="card card-front" aria-label="Business card front">
    <svg class="card-front__corner" viewBox="0 0 540 310" aria-hidden="true">
      <path d="M540 120 L540 294 Q540 310 524 310 L330 310 Q470 300 540 120 Z" fill="var(--brand-blue)"/>
    </svg>
    <div class="card-front__relief" role="img" aria-label="Large embossed brand mark"></div>

    <div class="wordmark">
      <div class="wordmark__name">QUARROW</div>
      <div class="wordmark__line">SIGNAL INSTRUMENTS</div>
    </div>

    <div class="person">
      <div class="person__name"><span class="person__bar"></span>AVERY HOLT</div>
      <div class="person__role">Manager</div>
    </div>

    <ul class="contact">
      <li class="no-icon">Your Address, City</li>
      <li class="no-icon">State, Zip 0000</li>
      <li>
        <svg viewBox="0 0 12 12"><path d="M3 1 L5 3.5 L4 5 Q5 7 7 8 L8.5 7 L11 9 L9.5 11 Q5 11 1 5 Q1 2 3 1 Z" fill="var(--brand-blue)"/></svg>
        123-456-2100
      </li>
      <li>
        <svg viewBox="0 0 12 12"><rect x="1" y="2.5" width="10" height="7" fill="none" stroke="var(--ink-soft)" stroke-width="1"/><path d="M1 2.5 L6 7 L11 2.5" fill="none" stroke="var(--ink-soft)" stroke-width="1"/></svg>
        youremail@quarrowmail.com
      </li>
      <li>
        <svg viewBox="0 0 12 12"><circle cx="6" cy="6" r="5" fill="none" stroke="var(--brand-blue)"/><ellipse cx="6" cy="6" rx="2.2" ry="5" fill="none" stroke="var(--brand-blue)"/><path d="M1 6 H11" stroke="var(--brand-blue)"/></svg>
        www.yourwebsite.com
      </li>
    </ul>
  </section>

  <section class="card card-back" aria-label="Business card back">
    <div class="card-back__pattern" role="img" aria-label="Raised repeating brand mark texture"></div>
    <div class="back-mark">
      <div class="back-mark__row">
        <span class="back-mark__dot"></span>
        <span class="back-mark__name">QUARROW</span>
      </div>
      <div class="back-mark__line">SIGNAL INSTRUMENTS</div>
    </div>
  </section>

</main>
</body>
</html>
```